Graphic design on webpages considering optimisation

Hi,

I would like to make the pages of my website look better. The looks must tie with the landing page, which I will not change.

Ping me an email with any questions. I have been on Pixel Harbour for the brimtower.com page and am very pleased with its looks.

Industry/Entity Type

Graphic Design

```html
<!DOCTYPE html>
<html lang="fr">
<head>
<meta charset="utf-8">
<title>Brimtower – Valeurs Ajoutées</title>
<link href="https://fonts.googleapis.com/css2?family=Open+Sans:wght@400;600;700;800&display=swap" rel="stylesheet">
<style>
:root{
  --ink:#222;
  --text:#333;
  --muted:#888;
  --line:#e2e2e2;
  --green:#8bb05a;
  --blue:#2d5a84;
  --orange:#f0911f;
  --red:#b84a4a;
  --side:#6d6d6d;
  --side-line:#5d5d5d;
  --dark:#111;
  --link-green:#86ac52;
  --play:#3fb44a;
}
*{box-sizing:border-box;margin:0;padding:0}
html,body{width:863px;height:1200px;overflow:hidden;background:#fff;font-family:"Open Sans",sans-serif;color:var(--text)}
.page{position:relative;width:863px;height:1200px}
.brand{position:absolute;left:130px;top:29px;font-weight:800;font-size:22px;letter-spacing:1px;color:#777}
.phone{position:absolute;right:129px;top:33px;font-size:12px;color:var(--ink);display:flex;align-items:center;gap:8px}
.phone svg{width:16px;height:16px}
.nav{position:absolute;left:130px;top:82px;width:604px;height:36px;border:1px solid var(--line);background:#f7f7f7;display:flex}
.nav a{font-size:9.5px;color:var(--ink);text-decoration:none;display:flex;align-items:center;justify-content:center;border-right:1px solid var(--line)}
.nav a:last-child{border-right:0}
.tiles{position:absolute;left:130px;top:137px;width:604px;height:110px;display:flex;justify-content:space-between}
.tile{width:143px;height:110px;position:relative;color:#fff}
.tile .art{position:absolute;left:26px;top:16px;width:94px;height:60px;border-radius:30px;background:radial-gradient(ellipse at 50% 40%,rgba(255,255,255,.9),rgba(255,255,255,.55) 60%,rgba(255,255,255,.15))}
.tile .label{position:absolute;left:13px;bottom:11px;font-weight:700;font-size:9.5px;line-height:12px;letter-spacing:0;white-space:nowrap}
.tile.red .label{font-size:9px}
.tile .go{position:absolute;right:12px;bottom:7px;width:19px;height:19px}
.green{background:var(--green)}.blue{background:var(--blue)}.orange{background:var(--orange)}.red{background:var(--red)}
.side{position:absolute;left:130px;top:267px;width:143px}
.menu a{display:block;height:29.6px;line-height:29.6px;padding-left:17px;background:var(--side);border-bottom:1px solid var(--side-line);color:#fff;font-size:9px;text-decoration:none}
.contact{margin-top:7px;padding:2px;border:1px solid var(--line)}
.contact div{background:linear-gradient(#3a3a3a,#111);height:48px;padding:9px 0 0 16px;color:#fff;font-size:11px;font-weight:700}
.contact small{display:block;font-size:5.5px;color:#777;font-weight:400;letter-spacing:.5px;margin-top:4px}
.partners{margin-top:10px;height:62px;border:1px solid var(--line);background:#f7f7f7;padding:7px 14px}
.partners h4{font-size:8.5px;font-weight:600;color:var(--ink)}
.partner-mark{display:flex;align-items:center;gap:6px;margin-top:8px;font-size:11px;font-weight:700;color:#222}
.partner-mark span{width:26px;height:26px;background:var(--blue)}
.benefits{margin-top:17px;height:32px;background:var(--green);color:#fff;font-size:11.5px;font-weight:600;line-height:32px;padding-left:12px}
.case{margin-top:10px;height:149px;border:1px solid var(--line);text-align:center;padding-top:10px}
.case .name{font-size:9px;font-weight:800;color:#c22}
.case .shot{width:52px;height:48px;margin:8px auto 8px;background:linear-gradient(#6f7a5e,#8a4a2e 70%,#3a2a20)}
.case p{font-size:6.6px;line-height:8.6px;color:#222}
.main{position:absolute;left:290px;top:262px;width:444px}
.main h1{font-size:15.5px;font-weight:600;color:var(--ink);padding-bottom:9px;border-bottom:1px solid var(--line)}
.main p,.main li{font-size:6.8px;line-height:13.6px;color:var(--text)}
.intro{margin-top:12px}
.intro p+p{margin-top:13px}
.main h2{font-size:11px;font-weight:400;color:var(--ink);margin:11px 0 9px}
ul.chev{list-style:none}
ul.chev li{position:relative;padding-left:16px;margin-bottom:8px}
ul.chev li::before{content:"›";position:absolute;left:0;top:0;color:#777}
.spec>li{list-style:none;position:relative;padding-left:15px;margin-bottom:4px}
.spec>li::before{content:"";position:absolute;left:0;top:5px;width:5px;height:5px;border-radius:50%;background:#111}
.spec .title{color:var(--link-green);font-size:8.5px;margin-bottom:6px}
.spec ul.chev li{margin-bottom:7px}
.foot{position:absolute;left:130px;top:1128px;width:604px;height:72px;background:var(--dark);color:#ddd}
.foot nav{position:absolute;left:17px;top:22px;font-size:7.5px}
.foot nav a{color:#ddd;text-decoration:none}
.foot .copy{position:absolute;left:17px;top:45px;font-size:7px}
.social{position:absolute;right:24px;top:24px;display:flex;gap:8px}
.social span{width:21px;height:21px;border-radius:50%;border:2px solid #333}
</style>
</head>
<body>
<div class="page">
  <div class="brand">BRIMTOWER</div>
  <div class="phone"><svg viewBox="0 0 16 16"><rect width="16" height="16" rx="2" fill="#3a7fd0"/><path d="M5 3l2 3-1 1c1 2 2 3 3 3l1-1 3 2-1 2c-4 0-8-4-8-8z" fill="#fff"/></svg>+33(0)100 555 010</div>

  <nav class="nav">
    <a style="width:79px">Accueil</a><a style="width:79px">Produits</a><a style="width:110px">Valeurs Ajoutees</a><a style="width:74px">Clients</a><a style="width:74px">Service</a><a style="width:74px">Societe</a><a style="width:114px">Contact</a>
  </nav>

  <div class="tiles">
    <div class="tile green"><div class="art" role="img" aria-label="Illustration nuage avec engrenage"></div><span class="label">MANUFACTURING</span><svg class="go" viewBox="0 0 19 19"><circle cx="9.5" cy="9.5" r="9.5" fill="#333"/><path d="M7.5 5.5v8l6-4z" fill="var(--play)"/></svg></div>
    <div class="tile blue"><div class="art" role="img" aria-label="Illustration nuage avec camion"></div><span class="label">DISTRIBUTION</span><svg class="go" viewBox="0 0 19 19"><circle cx="9.5" cy="9.5" r="9.5" fill="#333"/><path d="M7.5 5.5v8l6-4z" fill="var(--play)"/></svg></div>
    <div class="tile orange"><div class="art" role="img" aria-label="Illustration nuage avec globe"></div><span class="label">SERVICE</span><svg class="go" viewBox="0 0 19 19"><circle cx="9.5" cy="9.5" r="9.5" fill="#333"/><path d="M7.5 5.5v8l6-4z" fill="var(--play)"/></svg></div>
    <div class="tile red"><div class="art" role="img" aria-label="Illustration nuage avec loupe"></div><span class="label">HEBERGER OU PAS?</span><svg class="go" viewBox="0 0 19 19"><circle cx="9.5" cy="9.5" r="9.5" fill="#333"/><path d="M5.5 7.5h8l-4 6z" fill="#fff"/></svg></div>
  </div>

  <aside class="side">
    <div class="menu"><a>Nos Services</a><a>Conseil</a><a>Support</a><a>Development</a><a>Formation</a><a>Decouverte</a></div>
    <div class="contact"><div>Contactez nous<small>UNE INFO ?</small></div></div>
    <div class="partners"><h4>Nos partenariats</h4><div class="partner-mark"><span></span>CLOUDLEDGER</div></div>
    <div class="benefits">Bénéfices client</div>
    <div class="case"><div class="name">Maison Vell</div><div class="shot" role="img" aria-label="Capture du site client"></div><p>Passé de 85 M$ à 130 M$<br>(meme effectif),<br>Temps traitement à livraison<br>(amélioré de 25%),</p></div>
    <div class="case"><div class="name">Maison Vell</div><div class="shot" role="img" aria-label="Capture du site client"></div><p>Passé de 85 M$ à 130 M$<br>(meme effectif),<br>Temps traitement à livraison<br>(amélioré de 25%),</p></div>
    <div class="case"><div class="name">Maison Vell</div><div class="shot" role="img" aria-label="Capture du site client"></div><p>Passé de 85 M$ à 130 M$<br>(meme effectif),<br>Temps traitement à livraison<br>(amélioré de 25%),</p></div>
  </aside>

  <main class="main">
    <h1>Valeurs Ajoutées</h1>
    <div class="intro">
      <p>La très grande majorité d'entre vous est aujourd'hui déjà équipée en progiciel de gestion, alors on peut se demander légitimement : pourquoi changer ?</p>
      <p>Parce que la suite logicielle CloudLedger apporte de réels bénéfices, que l'on va détailler ci-dessous… et illustrer de manière personnalisée à votre cas, si vous nous laissez quelques petites informations dans le formulaire suivant : remplir le formulaire</p>
    </div>
    <h2>Les bénéfices communs à tous les produits CloudLedger :</h2>
    <ul class="chev">
      <li>Les logiciels CloudLedger sont accessibles via internet en ce qu'on appelle le mode SaaS ou autrement dit dans le Cloud. A moins que vous n'en soyez pas équipés (ce qui devient extrêmement rare) ou que votre Fournisseur d'Accès Internet ne parvient pas à vous fournir un débit raisonnable, vous pourrez profiter de :</li>
      <li>Un tarif hyper concurrentiel pour l'utilisation d'un progiciel de gestion (que ce soit l'ERP, le e-commerce, le CRM, CloudLedger One-World) : en effet, dans le tarif qui vous est proposé, c'est CloudLedger qui s'occupe de toute la partie machine, administration, sauvegarde, réparation, interventions quelconques sur le système d'exploitation ou l'application (hormis d'éventuels développements spécifiques que vous souhaiteriez), équipements tels que salle machine, climatisation, personnel technique, licences, mises à jour, maintenance (support technique en version anglaise en standard, nous consulter pour un support technique en version française)…d'où des économies substantielles.</li>
      <li>Une réactivité hors du commun grâce aux accès internet, de n'importe quel support électronique, PC, MAC, tablettes, smartphones,…, de n'importe où (zone couverte par internet ou les réseaux mobiles), à n'importe quel moment.</li>
      <li>Des économies conséquentes grâce à l'optimisation du fonctionnement opérationnel : quel que soit le module choisi, par exemple, juste la finance-comptabilité, des processus automatisés apportent rapidité de traitement, taux d'erreurs moindre, réduction de délais de facturation et de paiement, d'où des impacts financiers positifs ou autre exemple : grâce à la gestion des stocks multi-sites, multicanaux, quel que soit le produit acheté par l'un de vos canaux de distribution (points de vente physiques, vente en ligne, vente indirecte via des distributeurs,…), le stock est mis à jour en temps réel, les simulations basées sur l'historique des ventes, éventuellement corrigées de votre vision de gestionnaire expérimenté, évitent ruptures de stocks tout en les maintenant au niveau optimum.</li>
      <li>Une rapidité généralisée à tout ce que touche le logiciel CloudLedger : outre l'aspect financier, c'est la satisfaction avant tout de vos Clients (et Employés qui sont également impactés) qui en ressortira grandie. Grâce aux processus automatisés (workflows), aux procédures de traitement et d'approbation correspondant aux bonnes pratiques du monde entier et aux personnalisations éventuelles que vous souhaiterez apporter, tout est accéléré, les pertes de temps évitées, les tâches dévalorisantes ou difficiles remplacées par plus de temps et d'attention consacrés au service Client.</li>
    </ul>
    <h2>Les bénéfices spécifiques à:</h2>
    <ul class="spec">
      <li><div class="title">CloudLedger CRM+:</div>
        <ul class="chev">
          <li>Grâce à la visibilité sur l'intégralité des interactions (problèmes techniques remontés non résolus, litiges ou réclamations en cours, commandes non livrées, incidents de paiement, volume d'achat, centres d'intérêts,…) entre leurs Clients et leur entreprise, le travail collaboratif intra et interentreprises (référence positive sur une catégorie de produit par exemple, photo d'un produit, citation d'un Client, retour d'expérience d'un collègue,…), les commerciaux peuvent adopter les comportements les plus adaptés pour optimiser leurs relations d'affaires</li>
          <li>Grâce à l'automatisation de tâches chronophages telles que l'élaboration des prévisions commerciales et à la fourniture aisée et rapide de statistiques ad-hoc sur l'efficacité des campagnes markéting, les commerciaux peuvent se concentrer sur les bons champs d'exploration.</li>
        </ul>
      </li>
      <li><div class="title">CloudLedger E-Commerce :</div>
        <ul class="chev">
          <li>Grâce à la prise en compte des interactions Client du canal Web et mobile, la visibilité amont des Clients se renforce, permettant de solliciter en connaissance de cause une base de contacts, au travers de campagnes markéting ciblées sur leurs besoins.</li>
          <li>Grâce à la solution E-Commerce de CloudLedger, à sa facilité de mise en place et à son intégration avec l'ensemble des logiciels CloudLedger, l'entreprise peut optimiser la totalité de son fonctionnement opérationnel et stratégique, réduire ses points faibles et augmenter ses points forts.</li>
        </ul>
      </li>
    </ul>
  </main>

  <footer class="foot">
    <nav><a>Accueil</a> &nbsp;I&nbsp; <a>Modules</a> &nbsp;I&nbsp; <a>Services</a> &nbsp;I&nbsp; <a>Prix</a> &nbsp;I&nbsp; <a>Société</a> &nbsp;I&nbsp; <a>Contact</a></nav>
    <div class="copy">©2014 Brimtower , All Rights Reserved.</div>
    <div class="social"><span style="background:#3db4e4"></span><span style="background:#3b5a9a"></span><span style="background:#555"></span><span style="background:#e24c89"></span></div>
  </footer>
</div>
</body>
</html>
```